Corvane Paintless Dent Removal

Our company works on vehicles removing dents using a highly skilled trade which the metal is massaged out with special tools without disturbing the original paint, hence paintless dent removal. Besides keeping the paint and metal original its also very environmentally friendly since no paint or toxic fillers are used. Also we we are one of the most experienced companies in the business with 25 years

Target Market(s)

Retail Automobile consumers, Auto Dealerships and Auto Body Shops

Industry/Entity Type

Auto Repair

Contact Information for Business Card

Dale Hollister
PO Box 518 Brookmere, NY 11962
631-555-0148
corvanepdr@mailbox-example.com
website corvanepdr.example
youtube corvane paintless dent removal
25 years of experience removing Dents, Dings and Hail Damage

Font styles to use
Serif
Sans Serif

Colors

Designer to choose colors to be used in the design.

Requirements
Must have
• I do like things that are simple but classy and somewhat bold, also I like my logo so that should be somewhat important

```html
<!DOCTYPE html>
<html lang="en">
<head>
<meta charset="utf-8">
<title>Corvane Paintless Dent Removal – Business Card</title>
<link rel="stylesheet" href="https://fonts.googleapis.com/css2?family=Arimo:wght@400;700&display=swap">
<style>
  :root {
    --stage: #3a3431;
    --card: #121212;
    --card-edge: #1c1c1c;
    --green: #8cc63f;
    --blue: #1f4a86;
    --silver: #b9b9b9;
    --text: #e6e6e6;
    --rule: #4a4a4a;
  }
  * { margin: 0; padding: 0; box-sizing: border-box; }
  html, body { width: 1200px; height: 900px; overflow: hidden; }
  body {
    background: var(--stage);
    font-family: "Arimo", Arial, sans-serif;
    display: flex;
    align-items: center;
    justify-content: center;
    gap: 50px;
  }
  .card {
    position: relative;
    width: 525px;
    height: 300px;
    background: var(--card);
    border: 1px solid var(--card-edge);
    box-shadow: 0 10px 30px rgba(0,0,0,.45);
    overflow: hidden;
  }
  /* Front */
  .brand {
    position: absolute;
    top: 52px;
    left: 0;
    width: 100%;
    display: flex;
    align-items: center;
    justify-content: center;
    gap: 12px;
  }
  .brand__dot {
    width: 18px; height: 18px; border-radius: 50%;
    background: var(--green);
  }
  .brand__name {
    font-size: 22px;
    font-weight: 700;
    color: var(--blue);
    letter-spacing: .5px;
  }
  .rule {
    position: absolute;
    left: 180px;
    right: 40px;
    height: 1px;
    background: var(--rule);
  }
  .rule--top { top: 112px; left: 120px; right: 120px; }
  .rule--name { top: 178px; left: 230px; }
  .person {
    position: absolute;
    left: 36px;
    top: 166px;
    font-size: 21px;
    font-weight: 700;
    color: var(--green);
    text-transform: uppercase;
  }
  .contacts {
    position: absolute;
    left: 36px;
    top: 198px;
    list-style: none;
    color: var(--text);
    font-size: 15px;
    line-height: 21px;
  }
  .contacts li { display: flex; align-items: center; gap: 6px; }
  .contacts svg { width: 12px; height: 12px; fill: var(--green); flex: none; }
  .contacts .address { margin-top: 4px; font-size: 16px; }
  .channel {
    position: absolute;
    right: 36px;
    top: 128px;
    display: flex;
    align-items: center;
    gap: 10px;
  }
  .channel__label {
    color: var(--text);
    font-size: 14px;
    line-height: 17px;
    text-align: right;
  }
  .channel__mark {
    width: 26px; height: 26px; border-radius: 4px;
    background: var(--green);
  }
  /* Back */
  .card--back .brand { top: 110px; }
  .card--back .brand__name { color: var(--silver); font-size: 24px; }
  .card--back .brand__dot { background: var(--silver); }
  .tagline {
    position: absolute;
    right: 24px;
    bottom: 34px;
    color: var(--green);
    font-size: 13px;
  }
</style>
</head>
<body>

<section class="card card--front" aria-label="Business card front">
  <div class="brand">
    <span class="brand__dot"></span>
    <span class="brand__name">Corvane Paintless Dent Removal</span>
  </div>
  <div class="rule rule--top"></div>

  <div class="channel">
    <span class="channel__label">corvane paintless<br>dent removal</span>
    <span class="channel__mark"></span>
  </div>

  <h1 class="person">Dale Hollister</h1>
  <div class="rule rule--name"></div>

  <ul class="contacts">
    <li>
      <svg viewBox="0 0 12 12" aria-hidden="true"><path d="M2.5 1h2l1 2.5-1.3 1a6 6 0 0 0 3.3 3.3l1-1.3L11 7.5v2c0 .8-.7 1.5-1.5 1.5A8.5 8.5 0 0 1 1 2.5C1 1.7 1.7 1 2.5 1z"/></svg>
      631-555-0148
    </li>
    <li>
      <svg viewBox="0 0 12 12" aria-hidden="true"><rect x="0.5" y="2" width="11" height="8" rx="1"/><path d="M1 2.5l5 4 5-4" stroke="#121212" stroke-width="1" fill="none"/></svg>
      corvanepdr@mailbox-example.com
    </li>
    <li>
      <svg viewBox="0 0 12 12" aria-hidden="true"><circle cx="6" cy="6" r="5.5"/><path d="M.5 6h11M6 .5c2.5 3 2.5 8 0 11M6 .5c-2.5 3-2.5 8 0 11" stroke="#121212" stroke-width=".8" fill="none"/></svg>
      corvanepdr.example
    </li>
    <li class="address">PO Box 518 Brookmere, NY 11962</li>
  </ul>
</section>

<section class="card card--back" aria-label="Business card back">
  <div class="brand">
    <span class="brand__dot"></span>
    <span class="brand__name">Corvane Paintless Dent Removal</span>
  </div>
  <p class="tagline">25 years of experience removing Dents, Dings and Hail Damage</p>
</section>

</body>
</html>
```